Refer a Friend A5 Flyer for Healthcare Staff

We need an A5 flyer that we can hand out to existing and new staff members promoting our Refer a friend Scheme. We need the leaflet to encourage staff to talk to their family and friends about joining our Healthcare Agency, which provides staff to local care related establishments. Using our logo and brand colours blue and green, as per our website, the final design will need to clearly convey the benefits and attractions of referring additional staff to the team. In addition is the promotion of our Chatterbook page, requesting staff to like the page and to like and share various posts.

Target Market(s)

Healthcare and potential Healthcare Staff

Industry/Entity Type

Healthcare

Colors
33b8a4
3277b5

Requirements
Must have
• Company Logo, Brand colours,
• text; "Refer a Friend and receive a £50 Bonus after just 1 completed shift"
• text; "3 easy steps to refer a friend, 1 Fill out your name on the back of your Business Card 2 Hand the card to your friend or any person you wish to refer, 3 ask your friend to present the card to us when they attend their interview"
• text; "Like and share any of our Open Days on Chatterbook for a chance to win a prize, you can find us easily by searching @CarewellStaffingPartners"
• text; "Like our Page to stay up to date with our events and offers"
Nice to have
• care worker / elderly care / support worker pictures
• Content / pics from website www.carewellstaffingpartners.co.uk

```html
<!DOCTYPE html>
<html lang="en">
<head>
<meta charset="utf-8">
<title>Refer a Friend Flyer</title>
<link href="https://fonts.googleapis.com/css2?family=PT+Sans:ital,wght@0,400;0,700;1,400;1,700&family=Ubuntu+Condensed&family=Ubuntu:wght@300;500;700&display=swap" rel="stylesheet">
<style>
  :root {
    --brand-blue: #3277b5;
    --brand-green: #33b8a4;
    --band-blue: #2d5597;
    --text-blue: #2a5ea3;
    --paper: #ffffff;
    --backdrop: #d3e3e2;
  }
  * { margin: 0; padding: 0; box-sizing: border-box; }
  html, body { width: 1200px; height: 1000px; overflow: hidden; }
  body {
    background: var(--backdrop);
    font-family: "PT Sans", Arial, sans-serif;
    position: relative;
  }
  .flyer {
    position: absolute;
    left: 270px; top: 33px;
    width: 660px; height: 934px;
    background: var(--paper);
    overflow: hidden;
  }
  .hero-photo {
    position: absolute;
    left: 40px; top: 50px;
    width: 360px; height: 390px;
    background: linear-gradient(180deg, #ffffff 0%, #dde9f3 35%, #c4d8ea 70%, #ffffff 100%);
  }
  .brand-name {
    position: absolute;
    right: 40px; top: 100px;
    display: flex; align-items: center; gap: 10px;
    font-family: "Ubuntu", sans-serif;
    font-weight: 500;
    font-size: 30px;
    color: var(--brand-blue);
  }
  .brand-name .dot {
    width: 16px; height: 16px; border-radius: 50%;
    background: var(--brand-green);
  }
  .headline {
    position: absolute;
    right: 40px; top: 250px;
    text-align: left;
    font-family: "Ubuntu Condensed", "Ubuntu", sans-serif;
    font-size: 44px;
    line-height: 1.08;
    color: var(--brand-blue);
    letter-spacing: 0.5px;
  }
  .headline strong { font-family: "Ubuntu", sans-serif; font-weight: 500; font-size: 40px; }
  .headline .bonus { color: var(--brand-green); }
  .footnote {
    position: absolute;
    right: 40px; top: 400px;
    font-family: "Ubuntu Condensed", sans-serif;
    font-size: 18px;
    color: var(--brand-blue);
    letter-spacing: 0.3px;
  }
  .footnote b { font-family: "Ubuntu", sans-serif; font-weight: 700; font-size: 17px; }
  .steps-band {
    position: absolute;
    left: 0; top: 440px;
    width: 100%; height: 160px;
    background: var(--band-blue);
    color: #fff;
    padding: 24px 30px 0 40px;
  }
  .steps-title {
    display: flex; align-items: center; gap: 16px;
    font-weight: 700; font-style: italic; font-size: 21px;
  }
  .steps-title .num {
    width: 52px; height: 52px; border-radius: 50%;
    background: #fff; color: var(--brand-green);
    display: flex; align-items: center; justify-content: center;
    font-size: 30px; font-style: italic; font-weight: 700;
  }
  .steps-list {
    list-style: none;
    margin: 4px 0 0 84px;
    font-style: italic; font-size: 16.5px; line-height: 1.35;
  }
  .steps-list span { margin-right: 8px; }
  .care-photo {
    position: absolute;
    left: 0; top: 600px;
    width: 270px; height: 250px;
    background: linear-gradient(135deg, #7fb0d8 0%, #a9cfa0 45%, #d9e7ef 100%);
  }
  .social {
    position: absolute;
    left: 292px; top: 668px;
    width: 340px;
    color: var(--text-blue);
  }
  .social .lead { font-weight: 700; font-style: italic; font-size: 17px; line-height: 1.3; }
  .social .search { font-style: italic; font-size: 16px; margin-top: 2px; }
  .social .handle { font-weight: 700; font-size: 22px; margin-top: 4px; }
  .social .follow {
    margin-top: 18px;
    font-weight: 700; font-style: italic; font-size: 11.5px;
    text-transform: uppercase; letter-spacing: 0.4px;
    color: var(--brand-green);
  }
</style>
</head>
<body>
  <main class="flyer">
    <div class="hero-photo" role="img" aria-label="Group of healthcare staff in light blue scrubs joining hands in a team high five"></div>

    <div class="brand-name"><span class="dot"></span>Carewell Staffing</div>

    <h1 class="headline">
      <strong>REFER A FRIEND</strong> AND<br>
      RECEIVE A <strong class="bonus">£50 BONUS*</strong>
    </h1>
    <p class="footnote">* AFTER JUST <b>ONE</b> COMPLETED SHIFT</p>

    <section class="steps-band">
      <h2 class="steps-title"><span class="num">3</span>Easy Steps To Refer A Friend</h2>
      <ol class="steps-list">
        <li><span>1</span>Fill out your name on the back of your Business Card</li>
        <li><span>2</span>Hand the card to your friend or any person you wish to refer</li>
        <li><span>3</span>Ask your friend to present the card to us when they attend their interview</li>
      </ol>
    </section>

    <div class="care-photo" role="img" aria-label="Care worker in blue uniform holding hands with a smiling elderly woman outdoors"></div>

    <section class="social">
      <p class="lead">Like and share any of our Open Days on Chatterbook for a chance to win a prize,</p>
      <p class="search">you can find us easily by searching</p>
      <p class="handle">@CarewellStaffingPartners</p>
      <p class="follow">Like our page to stay up to date with our events and offers</p>
    </section>
  </main>
</body>
</html>
```